Satchel & Sundial needs new business card design

I need a new business card design. I'm looking for out-of-the-box design which represents the freedom of being a location independent entrepreneur.
I offer coaching, retreats and trips.
I would like to see designs with and without the photo.
Colors I use are black (#000000), green (#25A796) and brown (#D7C38C)
Website satchelandsundial.example

Target Market(s)

location independent entrepreneurs, digital nomads, people looking to swap the 9 to 5 for a lifestyle business

Industry/Entity Type

Business

Contact Information for Business Card

Dorota Falkner
Your Lifestyle Business Coach, Retreat & Trip Leader
http://satchelandsundial.example
hello@satchelandsundial.example
Live a life you don't need a holiday from

Font styles to use
Serif
Sans Serif

Requirements
Must have
• One side should contain only the logo. I would also consider having the "Live a life you don't need a holiday from" on that side too (depending on how it looks)
• Please show both sides on the designs.

```html
<!DOCTYPE html>
<html lang="en">
<head>
<meta charset="utf-8">
<title>Satchel &amp; Sundial — Business Card</title>
<link href="https://fonts.googleapis.com/css2?family=Open+Sans:wght@400;600;700&display=swap" rel="stylesheet">
<style>
  :root {
    --canvas: #2b2b2b;
    --card-light: #f4f4f2;
    --card-dark: #161616;
    --ink: #1c1c1c;
    --ink-soft: #3a3a3a;
    --brand-green: #25a796;
    --paper-white: #f2f2f2;
    --muted-white: #d8d8d8;
    --divider: #cfcfcf;
  }
  * { box-sizing: border-box; margin: 0; padding: 0; }
  html, body {
    width: 1200px; height: 900px; overflow: hidden;
    background: var(--canvas);
    font-family: "Open Sans", Arial, sans-serif;
  }
  .stage {
    position: relative; width: 1200px; height: 900px;
    display: flex; align-items: center; justify-content: center; gap: 40px;
  }
  .card {
    position: relative; width: 520px; height: 300px; border-radius: 18px;
    overflow: hidden; box-shadow: 0 10px 24px rgba(0,0,0,.35);
  }
  .card--front { background: var(--card-light); color: var(--ink); }
  .card--back {
    background: var(--card-dark); color: var(--paper-white);
    display: flex; flex-direction: column; align-items: center; justify-content: center;
  }

  /* Front side */
  .brand-name {
    position: absolute; left: 34px; top: 118px; width: 200px;
    font-weight: 700; font-size: 27px; line-height: 1.1; letter-spacing: .5px;
    color: var(--ink); text-transform: uppercase;
  }
  .divider {
    position: absolute; left: 248px; top: 36px; width: 1px; height: 170px;
    background: var(--divider);
  }
  .contact { position: absolute; left: 266px; top: 34px; right: 20px; }
  .person-name { color: var(--brand-green); font-weight: 600; font-size: 17px; }
  .person-title { font-size: 12.5px; line-height: 1.35; color: var(--ink-soft); margin-top: 2px; }
  .contact-list { list-style: none; margin-top: 72px; font-size: 12px; color: var(--ink-soft); }
  .contact-list li { display: flex; align-items: center; gap: 7px; line-height: 1.6; }
  .contact-list svg { flex: none; }
  .tagline {
    position: absolute; left: 0; right: 0; bottom: 34px; text-align: center;
    font-weight: 600; font-size: 15px; letter-spacing: 2.6px; text-transform: uppercase;
    color: var(--ink);
  }

  /* Back side */
  .brand-name--reverse {
    font-weight: 700; font-size: 34px; letter-spacing: .8px; text-transform: uppercase;
    color: var(--paper-white);
  }
  .services {
    margin-top: 26px; font-size: 12px; letter-spacing: 2px; color: var(--muted-white);
    text-transform: uppercase;
  }
</style>
</head>
<body>
<main class="stage">
  <section class="card card--front" aria-label="Business card front">
    <div class="brand-name">Satchel &amp; Sundial</div>
    <div class="divider"></div>
    <div class="contact">
      <p class="person-name">Dorota Falkner</p>
      <p class="person-title">Your Lifestyle Business Coach,<br>Retreat &amp; Trip Leader</p>
      <ul class="contact-list">
        <li>
          <svg width="10" height="8" viewBox="0 0 10 8" aria-hidden="true">
            <rect width="10" height="8" rx="1" fill="var(--brand-green)"/>
            <path d="M0.5 1 L5 4.5 L9.5 1" fill="none" stroke="#fff" stroke-width="1"/>
          </svg>
          hello@satchelandsundial.example
        </li>
        <li>
          <svg width="10" height="10" viewBox="0 0 10 10" aria-hidden="true">
            <circle cx="5" cy="5" r="5" fill="var(--brand-green)"/>
            <path d="M3 5 L5 3 M5 7 L7 5" stroke="#fff" stroke-width="1"/>
          </svg>
          www.satchelandsundial.example
        </li>
      </ul>
    </div>
    <p class="tagline">Live a life you don't need a holiday from</p>
  </section>

  <section class="card card--back" aria-label="Business card back">
    <div class="brand-name--reverse">Satchel &amp; Sundial</div>
    <p class="services">Coaching | Retreats | Trips</p>
  </section>
</main>
</body>
</html>
```